Redesign of business card for Cedar Ridge Mechanical

We are looking for a new design for our business cards for Cedar Ridge Mechanical. We are a plumbing & HVAC construction company, operating on the West Coast of Canada and USA. Logo attached.
Industry/Entity Type
Construction - Plumbing & HVAC
Contact Information for Business Card
Name, address, phone numbers, email, website address
Look and feel
Each slider illustrates characteristics of the customer's brand and the style your logo design should communicate.

```html
<!DOCTYPE html>
<html lang="en">
<head>
<meta charset="utf-8">
<title>Cedar Ridge Mechanical – Business Card</title>
<link rel="stylesheet" href="https://fonts.googleapis.com/css2?family=Montserrat:wght@400;600;700&display=swap">
<style>
  :root {
    --page-bg: #e4ded8;
    --card-clear: #e9e4de;
    --card-dark: #0d0d0d;
    --card-dark-edge: #2a2a2a;
    --sliver: #a9a39c;
    --name-color: #ddd3c8;
    --detail-color: #cbb9a3;
    --brand-color: #1c1c1c;
  }
  html, body {
    margin: 0;
    width: 1200px;
    height: 1047px;
    overflow: hidden;
    background: var(--page-bg);
  }
  .card {
    position: absolute;
    left: 100px;
    top: 250px;
    width: 1000px;
    height: 546px;
    border-radius: 24px;
    overflow: hidden;
    background: var(--card-clear);
    box-shadow: 0 10px 30px rgba(0,0,0,0.12);
    font-family: "Montserrat", sans-serif;
  }
  .card-shapes {
    position: absolute;
    inset: 0;
  }
  .contact {
    position: absolute;
    left: 38px;
    top: 0;
    color: var(--detail-color);
  }
  .contact-name {
    position: absolute;
    top: 184px;
    margin: 0;
    white-space: nowrap;
    font-size: 34px;
    font-weight: 700;
    letter-spacing: 1px;
    color: var(--name-color);
  }
  .contact-title {
    position: absolute;
    top: 228px;
    margin: 0;
    white-space: nowrap;
    font-size: 25px;
    font-weight: 400;
    color: var(--name-color);
  }
  .contact-address {
    position: absolute;
    top: 298px;
    margin: 0;
    white-space: nowrap;
    font-size: 25px;
    line-height: 38px;
    font-style: normal;
  }
  .contact-lines {
    position: absolute;
    top: 403px;
    margin: 0;
    padding: 0;
    list-style: none;
    font-size: 25px;
    line-height: 38.5px;
    white-space: nowrap;
  }
  .contact-lines li {
    display: flex;
    align-items: center;
    gap: 8px;
  }
  .contact-lines svg {
    width: 19px;
    height: 19px;
    fill: none;
    stroke: var(--detail-color);
    stroke-width: 2;
  }
  .brand {
    position: absolute;
    left: 618px;
    top: 108px;
    display: flex;
    align-items: center;
    gap: 16px;
    color: var(--brand-color);
  }
  .brand-mark {
    width: 30px;
    height: 30px;
    background: var(--brand-color);
  }
  .brand-name {
    margin: 0;
    font-size: 30px;
    font-weight: 600;
    line-height: 38px;
    letter-spacing: 1px;
    text-transform: uppercase;
  }
</style>
</head>
<body>
  <div class="card">
    <svg class="card-shapes" viewBox="0 0 1000 546" preserveAspectRatio="none" aria-hidden="true">
      <defs>
        <linearGradient id="darkPanel" x1="0" y1="0" x2="1" y2="1">
          <stop offset="0" stop-color="var(--card-dark-edge)"/>
          <stop offset="0.45" stop-color="var(--card-dark)"/>
          <stop offset="1" stop-color="var(--card-dark)"/>
        </linearGradient>
      </defs>
      <polygon points="0,0 353,0 752,546 0,546" fill="url(#darkPanel)"/>
      <polygon points="358,0 376,0 740,546 729,546" fill="var(--sliver)"/>
    </svg>

    <div class="contact">
      <h1 class="contact-name">DANIEL HART</h1>
      <p class="contact-title">Managing Director</p>
      <address class="contact-address">Your address, City<br>State, Zip 1234</address>
      <ul class="contact-lines">
        <li>
          <svg viewBox="0 0 24 24"><path d="M5 3h4l2 5-2.5 1.5a11 11 0 0 0 6 6L16 13l5 2v4a2 2 0 0 1-2 2A16 16 0 0 1 3 5a2 2 0 0 1 2-2z"/></svg>
          123 456 789
        </li>
        <li>
          <svg viewBox="0 0 24 24"><rect x="3" y="6" width="18" height="13" rx="1"/><path d="M3 7l9 7 9-7"/></svg>
          info@yourmail.com
        </li>
        <li>
          <svg viewBox="0 0 24 24"><circle cx="12" cy="12" r="9"/><path d="M3 12h18M12 3c3 3 3 15 0 18M12 3c-3 3-3 15 0 18"/></svg>
          www.yourwebsite.com
        </li>
      </ul>
    </div>

    <div class="brand">
      <span class="brand-mark"></span>
      <p class="brand-name">Cedar Ridge<br>Mechanical</p>
    </div>
  </div>
</body>
</html>
```